New Fun, Positive, energised looking Business Card Needed for High Achiever Coach

I am looking for a two sided full colour business card. I am self employed and have recently re branded my 1-2-1 work re-vitalising high achievers. My target client base for these cards is therefore high achievers - usually aged 40 -55, they are often entrepreneurs, CEO or work in banking and finance and 2/3 are male. I work with them on 90 day or 6 month coaching programs to help them live their success in a healthier, more sustainable and fulfiiled way. They pay for this privately so though they are corporate types the cards need not look 'corporate'. I want to portray the idea of transformation, vitality and re-connecting.
You can get a feel for the look I like on my new website: morvenlisk.co.uk
I want to use this logo with strapline (Re-Vitalising High Achievers) (I purchased off Logoharbor) and font/ colours (the turquoise and green).
Details to include on the card:
www.morvenlisk.co.uk
+44 7915 302618
morven@morvenlisk.co.uk
skype: morvenlisk
I'd also like to include:
Do you struggle to switch off? Want to be healthier and feel fitter? Want closer relationships? More clarity over the direction you are headed? I can help you do these things using integrated mind-body techniques. Visit morvenlisk.co.uk TODAY to apply for a FREE Breakthrough session.
BUT if that is too much text for a card I am open to advice/ammendments.
Updates
Thanks for your design - I am considering them. PLease change the wording to :

```html
<!DOCTYPE html>
<html lang="en">
<head>
<meta charset="utf-8">
<title>Morven Lisk – Business Card</title>
<link href="https://fonts.googleapis.com/css2?family=Open+Sans:wght@400;600;700&display=swap" rel="stylesheet">
<style>
  :root{
    --turquoise:#0aa5c8;
    --green:#5cb95f;
    --white:#ffffff;
    --stage:#e8e9ed;
    --card-radius:26px;
  }
  *{margin:0;padding:0;box-sizing:border-box}
  html,body{width:1200px;height:987px;overflow:hidden;background:var(--stage);font-family:"Open Sans",Arial,sans-serif}
  .canvas{position:relative;width:1200px;height:987px}
  .card{position:absolute;left:250px;width:700px;height:400px;border-radius:var(--card-radius);overflow:hidden;box-shadow:0 6px 18px rgba(0,0,0,.12)}
  .card--front{top:60px;background:var(--white)}
  .card--back{top:527px;background:var(--turquoise)}

  .front-waves{position:absolute;inset:0}

  .brand{position:absolute;top:52px;left:0;width:700px;text-align:center}
  .brand__name{display:inline-flex;align-items:center;gap:14px;font-weight:700;font-size:46px;color:var(--turquoise);line-height:1}
  .brand__dot{width:32px;height:32px;border-radius:50%;background:var(--green)}
  .brand__strapline{margin-top:10px;font-size:18px;font-weight:400;color:var(--turquoise);letter-spacing:.3px}

  .contact{position:absolute;color:var(--white);font-size:18px;line-height:1}
  .contact__item{display:flex;align-items:center;gap:9px;height:34px;white-space:nowrap}
  .contact__icon{width:17px;height:17px;flex:none}
  .contact--left{left:30px;top:296px}
  .contact--right{left:330px;top:322px}
  .contact__divider{position:absolute;left:314px;top:318px;width:1.5px;height:66px;background:rgba(255,255,255,.7)}

  .pitch{position:absolute;inset:0;display:flex;align-items:center;justify-content:center;padding:0 40px}
  .pitch__text{text-align:center;color:var(--white);font-size:22px;line-height:1.42}
  .pitch__text strong{font-weight:700}
</style>
</head>
<body>
<main class="canvas">

  <section class="card card--front" aria-label="Card front">
    <svg class="front-waves" width="700" height="400" viewBox="0 0 700 400" aria-hidden="true">
      <path d="M0,116 C220,146 470,216 700,361" fill="none" stroke="var(--green)" stroke-width="11"/>
      <path d="M0,140 C220,170 470,240 700,385 L700,400 L0,400 Z" fill="var(--turquoise)"/>
    </svg>

    <div class="brand">
      <div class="brand__name"><span class="brand__dot"></span>Morven Lisk</div>
      <div class="brand__strapline">Re-Vitalising High Achievers</div>
    </div>

    <div class="contact contact--left">
      <div class="contact__item">
        <svg class="contact__icon" viewBox="0 0 24 24" aria-hidden="true"><circle cx="12" cy="12" r="11" fill="none" stroke="#fff" stroke-width="2"/><path d="M8.5 6.5l2 2-1.2 1.6c.8 1.7 2 2.9 3.6 3.7l1.6-1.2 2 2-1.5 1.9c-3.8-.6-7.6-4.4-8.2-8.2z" fill="#fff"/></svg>
        <span>+44 7915 302618</span>
      </div>
      <div class="contact__item">
        <svg class="contact__icon" viewBox="0 0 24 24" aria-hidden="true"><rect x="2" y="5" width="20" height="14" rx="2" fill="#fff"/><path d="M3 6.5l9 6.5 9-6.5" fill="none" stroke="var(--turquoise)" stroke-width="1.8"/></svg>
        <span>morven@morvenlisk.co.uk</span>
      </div>
    </div>

    <div class="contact__divider"></div>

    <div class="contact contact--right">
      <div class="contact__item">
        <svg class="contact__icon" viewBox="0 0 24 24" aria-hidden="true"><circle cx="12" cy="12" r="10" fill="none" stroke="#fff" stroke-width="2"/><ellipse cx="12" cy="12" rx="4" ry="10" fill="none" stroke="#fff" stroke-width="1.6"/><path d="M2 12h20M4 7h16M4 17h16" stroke="#fff" stroke-width="1.4"/></svg>
        <span>www.morvenlisk.co.uk</span>
      </div>
      <div class="contact__item">
        <svg class="contact__icon" viewBox="0 0 24 24" aria-hidden="true"><circle cx="12" cy="12" r="10" fill="#fff"/></svg>
        <span>morvenlisk</span>
      </div>
    </div>
  </section>

  <section class="card card--back" aria-label="Card back">
    <div class="pitch">
      <p class="pitch__text">
        Do you struggle to switch off?<br>
        Want to be healthier and feel fitter?<br>
        Want closer relationships?<br>
        More clarity over the direction you are headed?<br>
        I can help you do these things using integrated<br>
        mind-body techniques.<br>
        Visit <strong>morvenlisk.co.uk</strong> TODAY to apply for a<br>
        FREE Breakthrough session.
      </p>
    </div>
  </section>

</main>
</body>
</html>
```